Corvane Freight Company Business Card Design

We are a company that delivers natural saltwater (from the ocean) to aquarium companies, restaurants and home marine tanks. I would like a new business card to suit.

Must include Name, company name, abn, contact number and website as well as logo (see attached).

Looking for a design that stands out, has a clean but unique appearance.

Double and single sided entries welcome

Business

• Logo

```html
<!DOCTYPE html>
<html lang="en">
<head>
<meta charset="utf-8">
<title>Corvane Freight Company – Business Card</title>
<link href="https://fonts.googleapis.com/css2?family=Source+Sans+3:wght@400;600;700&display=swap" rel="stylesheet">
<style>
  :root {
    --stage: #161616;
    --card-blue: #3170e8;
    --card-line: #7fb0ff;
    --tab-light: #cdeeff;
    --tab-mid: #8fd6fb;
    --ink-white: #ffffff;
    --ink-soft: #e6eeff;
    --ink-dark: #0b0b0b;
    --divider: #ff9a8a;
  }
  * { margin: 0; padding: 0; box-sizing: border-box; }
  html, body {
    width: 1200px; height: 415px; overflow: hidden;
    background: var(--stage);
    font-family: "Source Sans 3", "Myriad Pro", Arial, sans-serif;
  }
  .stage { position: relative; width: 1200px; height: 415px; }
  .card {
    position: absolute; top: 51px;
    width: 537px; height: 307px;
    border-radius: 28px;
    background: var(--card-blue);
    overflow: hidden;
  }
  .card--front { left: 49px; }
  .card--back { left: 623px; }

  .brand-name {
    position: absolute;
    color: var(--ink-white);
    font-weight: 700;
    line-height: 1.02;
    letter-spacing: 0.2px;
  }
  .card--front .brand-name {
    left: 32px; top: 34px;
    font-size: 38px;
  }
  .card--back .brand-name {
    left: 0; right: 0; top: 100px;
    text-align: center;
    font-size: 44px;
  }

  .name-rule {
    position: absolute; left: 0; top: 169px;
    width: 330px; height: 1.5px;
    background: var(--card-line);
  }
  .name-tab {
    position: absolute; left: 323px; top: 148px;
    width: 230px; height: 44px;
    border-radius: 14px 0 0 14px;
    background: linear-gradient(180deg, var(--tab-light) 0%, var(--tab-mid) 100%);
    box-shadow: 0 0 10px rgba(190, 235, 255, 0.55);
    display: flex; align-items: center;
    padding-left: 22px;
    color: var(--ink-dark);
    font-size: 21px;
  }
  .name-tab strong { font-weight: 700; margin-right: 5px; }

  .contact-list {
    position: absolute; left: 29px; top: 207px;
    list-style: none;
    color: var(--ink-soft);
    font-size: 13px;
    line-height: 21px;
  }
  .contact-list li { display: flex; align-items: center; gap: 4px; }
  .contact-list svg { width: 11px; height: 11px; }

  .address {
    position: absolute; left: 172px; top: 227px;
    padding-left: 14px;
    border-left: 1px solid var(--divider);
    color: var(--ink-soft);
    font-size: 13px;
    line-height: 19px;
  }
  .address strong { font-weight: 700; color: var(--ink-white); }

  .back-web {
    position: absolute; left: 0; right: 0; top: 244px;
    text-align: center;
    color: var(--ink-soft);
    font-size: 17px;
    letter-spacing: 3.2px;
  }
</style>
</head>
<body>
<div class="stage">

  <section class="card card--front">
    <div class="brand-name">Corvane Freight<br>Company</div>

    <div class="name-rule"></div>
    <div class="name-tab"><strong>Your name,</strong>Title</div>

    <ul class="contact-list">
      <li>
        <svg viewBox="0 0 12 12" aria-hidden="true"><circle cx="6" cy="6" r="5.5" fill="var(--ink-soft)"/><path d="M4 3.2l1 1.4-.6.7a4 4 0 0 0 2.3 2.3l.7-.6 1.4 1-.5.9c-2.6-.4-4.4-2.2-4.8-4.8z" fill="var(--card-blue)"/></svg>
        123-456-7890
      </li>
      <li>
        <svg viewBox="0 0 12 12" aria-hidden="true"><circle cx="6" cy="6" r="5.5" fill="var(--ink-soft)"/><path d="M1 6h10M6 1c-2 2.8-2 7.2 0 10M6 1c2 2.8 2 7.2 0 10" stroke="var(--card-blue)" stroke-width=".8" fill="none"/></svg>
        www.website.com
      </li>
      <li>ABN : 0123456789</li>
    </ul>

    <div class="address">
      <strong>Corvane Freight Company</strong><br>
      Street Name, City Name, State, City Zip Code
    </div>
  </section>

  <section class="card card--back">
    <div class="brand-name">Corvane Freight<br>Company</div>
    <div class="back-web">www.website.com</div>
  </section>

</div>
</body>
</html>
```